New Business Cards for NYC Salon

We are updating all of our cards. 7142-8863-2095 is my account number. We put names of our stylists on their cards. The back should include appointment space. Were looking for something more sleek and modern. Black/White Silver... or even touches of the orange color on our website which has been our thing for years. The design should communicate professional upscale boutique salon for men and women. Should be able to incorporate design into thank you cards, referral cards, brochure and postcards. The file is a zip file...we like the stacked ones black or white or the side versions.

Industry/Entity Type

Beauty Salon

Contact Information for Business Card

Marcus John's Salon313 W. 53rd Street, New York NY 10019 212-683-2741 info@marcusellingsalon.example www.marcusellingsalon.example

Font styles to use
Other font styles liked:
• trajan

Requirements
Must have
• we print a different card for every person in the salon. Begin by designing with the name Marcus. We will change it with every employee when printing. Must have a space for appointment date and time.
Nice to have
• Were looking to move towards the stacked or side placed logo but not opposed to utilizing the circular.
Should not have
• Photos

```html
<!DOCTYPE html>
<html lang="en">
<head>
<meta charset="utf-8">
<title>Marcus Elling's Salon – Business Card</title>
<link rel="stylesheet" href="https://fonts.googleapis.com/css2?family=Source+Sans+3:ital,wght@0,400;0,600;1,600&display=swap">
<style>
  :root {
    --backdrop: #d9d9d7;
    --card: #0b0b0b;
    --card-edge: #1c1c1c;
    --ink: #ffffff;
    --ink-soft: #d8d8d8;
    --rule: #8a8a8a;
  }
  * { box-sizing: border-box; margin: 0; padding: 0; }
  html, body { width: 1200px; height: 900px; overflow: hidden; }
  body {
    background: var(--backdrop);
    font-family: "Source Sans 3", "Segoe UI", Arial, sans-serif;
    color: var(--ink);
    position: relative;
  }
  .card {
    position: absolute;
    width: 580px;
    height: 330px;
    background: radial-gradient(ellipse at 40% 40%, var(--card-edge), var(--card) 70%);
    border-radius: 4px;
    box-shadow: 0 10px 24px rgba(0,0,0,.25);
  }
  /* Appointment side */
  .card-back { left: 520px; top: 90px; padding: 30px 40px; }
  .appointment-title {
    text-align: center;
    font-weight: 600;
    font-size: 22px;
    margin-bottom: 14px;
  }
  .field { display: flex; align-items: flex-end; font-size: 14px; color: var(--ink-soft); height: 36px; }
  .field-label { width: 58px; }
  .field-line { flex: 1; border-bottom: 1px solid var(--rule); height: 18px; margin-bottom: 4px; }
  .field-suffix { margin: 0 12px; }
  .field-suffix:last-child { margin-right: 0; }
  .notice {
    margin-top: 34px;
    text-align: center;
    font-style: italic;
    font-weight: 600;
    font-size: 15px;
  }
  /* Front side */
  .card-front { left: 120px; top: 470px; }
  .brand-mark {
    position: absolute; right: 40px; top: 40px;
    display: flex; align-items: center; gap: 10px;
    font-size: 18px; font-weight: 400; color: var(--ink);
  }
  .brand-dot { width: 14px; height: 14px; border-radius: 50%; background: var(--ink); flex: none; }
  .salon-name {
    position: absolute; left: 36px; top: 92px;
    font-weight: 600; font-size: 26px;
  }
  .contact-list {
    position: absolute; right: 36px; bottom: 30px;
    list-style: none; text-align: right;
    font-size: 18px; line-height: 1.3;
  }
  .contact-list li { display: flex; justify-content: flex-end; align-items: flex-start; gap: 12px; }
  .contact-list svg { width: 16px; height: 16px; margin-top: 4px; flex: none; fill: var(--ink); }
  .contact-address { margin-top: 6px; }
</style>
</head>
<body>
  <section class="card card-back" aria-label="Appointment card">
    <h2 class="appointment-title">Your Next Appointment is</h2>
    <div class="field"><span class="field-label">Name :</span><span class="field-line"></span></div>
    <div class="field"><span class="field-label">Date :</span><span class="field-line"></span></div>
    <div class="field field-time">
      <span class="field-label">Time:</span><span class="field-line"></span>
      <span class="field-suffix">AM</span><span class="field-line"></span>
      <span class="field-suffix">PM</span>
    </div>
    <p class="notice">If unable to keep appointment, kindly give 24hrs notice.</p>
  </section>

  <section class="card card-front" aria-label="Business card">
    <div class="brand-mark"><span class="brand-dot"></span><span>Marcus Elling's Salon</span></div>
    <h1 class="salon-name">Marcus Elling's Salon</h1>
    <ul class="contact-list">
      <li><span>212-683-2741</span>
        <svg viewBox="0 0 16 16" aria-hidden="true"><path d="M3 2h3l1.5 3.5-2 1.2a8 8 0 0 0 3.8 3.8l1.2-2L14 10v3a1 1 0 0 1-1 1A11 11 0 0 1 2 3a1 1 0 0 1 1-1z"/></svg></li>
      <li><span>info@marcusellingsalon.example</span>
        <svg viewBox="0 0 16 16" aria-hidden="true"><path d="M1 3h14v10H1z M2.5 4.5 8 9l5.5-4.5v-.2H2.5z" fill-rule="evenodd"/></svg></li>
      <li><span>marcusellingsalon.example</span>
        <svg viewBox="0 0 16 16" aria-hidden="true"><path d="M6.5 9.5l3-3M5 8 3.5 9.5a2.1 2.1 0 0 0 3 3L8 11M11 8l1.5-1.5a2.1 2.1 0 0 0-3-3L8 5" stroke="#fff" stroke-width="1.6" fill="none" stroke-linecap="round"/></svg></li>
      <li class="contact-address"><span>742 E. 18th Street,<br>New York NY 10003</span>
        <svg viewBox="0 0 16 16" aria-hidden="true"><path d="M8 1a5 5 0 0 1 5 5c0 3.5-5 9-5 9S3 9.5 3 6a5 5 0 0 1 5-5zm0 3a2 2 0 1 0 0 4 2 2 0 0 0 0-4z" fill-rule="evenodd"/></svg></li>
    </ul>
  </section>
</body>
</html>
```